Corportate Power Point Template

We need a corporate PPT Design for our startup Big Data company.

Basically, our company will ingest, analyze and generate dynamic Dashboards with data consumed from different sources like Social Networks, Enterprise Legacy Systems such as e-Commerce, ERP, CRM and others.

Company is headquartered in Brazil, but will have a global presence.

Industry/Entity Type

It Company

```html
<!DOCTYPE html>
<html lang="en">
<head>
<meta charset="utf-8">
<title>Project Title Here</title>
<link rel="stylesheet" href="https://fonts.googleapis.com/css2?family=Open+Sans:wght@600;700&family=Roboto+Condensed:wght@400&display=swap">
<style>
  :root {
    --orange: #f26a21;
    --orange-soft: #f9a86a;
    --peach: #fde3cf;
    --ink: #1d1d1d;
    --text: #2b2b2b;
    --white: #ffffff;
    --footer-bg: #f6f2ef;
  }
  * { margin: 0; padding: 0; box-sizing: border-box; }
  html, body { width: 1200px; height: 900px; overflow: hidden; background: var(--white); }
  .slide {
    position: relative;
    width: 1200px;
    height: 900px;
    overflow: hidden;
    font-family: "Roboto Condensed", "Arial Narrow", sans-serif;
    color: var(--text);
  }
  .backdrop {
    position: absolute;
    inset: 0;
    background:
      radial-gradient(ellipse 900px 700px at 0% 30%, rgba(249,168,106,0.75) 0%, rgba(253,227,207,0.6) 45%, rgba(255,255,255,0) 80%),
      linear-gradient(120deg, var(--peach) 0%, #fff5ee 55%, var(--white) 100%);
  }
  .brand {
    position: absolute;
    top: 355px;
    left: 0;
    width: 100%;
    display: flex;
    justify-content: center;
    align-items: center;
    gap: 22px;
  }
  .brand-mark {
    width: 58px;
    height: 58px;
    background: var(--orange);
  }
  .brand-name {
    font-family: "Open Sans", Arial, sans-serif;
    font-weight: 600;
    font-size: 78px;
    line-height: 1;
    color: var(--orange);
    letter-spacing: -1px;
  }
  .title-block {
    position: absolute;
    top: 510px;
    left: 0;
    width: 100%;
    text-align: center;
  }
  .project-title {
    font-family: "Open Sans", Arial, sans-serif;
    font-weight: 600;
    font-size: 49px;
    line-height: 1.2;
    color: var(--ink);
  }
  .project-title .accent { color: var(--orange); }
  .subtext {
    margin-top: 20px;
    font-size: 23px;
    line-height: 36px;
    color: var(--text);
  }
  .presenter {
    margin-top: 24px;
  }
  .presenter-label {
    font-size: 22px;
    line-height: 30px;
    color: var(--text);
  }
  .presenter-name {
    font-size: 27px;
    line-height: 36px;
    color: var(--orange);
  }
  .footer {
    position: absolute;
    left: 0;
    bottom: 0;
    width: 100%;
    height: 63px;
    background: linear-gradient(180deg, var(--white) 0%, var(--footer-bg) 100%);
    border-top: 3px solid var(--orange);
    display: flex;
    justify-content: space-between;
    align-items: center;
    padding: 0 14px;
    font-size: 19px;
  }
  .copyright { color: var(--ink); }
  .page-number { color: var(--orange); }
</style>
</head>
<body>
  <main class="slide">
    <div class="backdrop" role="img" aria-label="Soft orange halftone dot pattern background"></div>

    <div class="brand">
      <span class="brand-name">Northvale Data</span>
      <span class="brand-mark"></span>
    </div>

    <section class="title-block">
      <h1 class="project-title"><span class="accent">Project</span> Title Here</h1>
      <p class="subtext">Subtext here Subtext here Subtext here Subtext here<br>Subtext here Subtext here Subtext here</p>
      <div class="presenter">
        <p class="presenter-label">Persentatator Name</p>
        <p class="presenter-name">Marina Costa</p>
      </div>
    </section>

    <footer class="footer">
      <span class="copyright">Copyright text here</span>
      <span class="page-number">Page 01</span>
    </footer>
  </main>
</body>
</html>
```